Book Title: Quiet Harbors -- Notes From a Restless Pulpit Today

I am looking for just the book cover design, do not need spine or back cover art.

This book is a memoir and the cover needs to be prepared for print and ebook applications.

The part of the title that follows the dash ("Notes From a Restless Pulpit Today") is not a subtitle but a tag and can be separated from the title itself.

I am inclined to a traditional design with "modern and minimalist" tendencies. I like graphic images that convey the idea of a "journey" or "quest". The memoir is about my pastoral work as a Christian minister but it is not a "religious" book. I do not want churches or any traditional religious symbols on the cover. In fact this book is directed toward those who have little, if any, interest in organized religion of any kind and if that could somehow be captured in the cover art it would be useful.

I am attaching a file with some sample cover art designs that I like or do not like to help guide your thinking. I am open to your interpretation and creative thinking. This book is a labor of love and I want the cover art to reflect my deep thinking on the topic.

```html
<!DOCTYPE html>
<html lang="en">
<head>
<meta charset="utf-8">
<title>Quiet Harbors — Book Cover</title>
<link rel="stylesheet" href="https://fonts.googleapis.com/css2?family=Cinzel:wght@400;500&family=Montserrat:wght@600&display=swap">
<style>
  :root {
    --paper: #fafafb;
    --title-blue: #536a98;
    --tag-mauve: #a99bb0;
    --author-slate: #5b6470;
    --water-light: #d9dbe2;
    --water-mid: #a9adbb;
    --hull-dark: #100f15;
  }
  html, body {
    margin: 0;
    padding: 0;
    overflow: hidden;
    background: var(--paper);
  }
  .cover {
    position: relative;
    width: 800px;
    height: 1200px;
    background: var(--paper);
    overflow: hidden;
  }
  .title {
    position: absolute;
    left: 0;
    right: 0;
    top: 96px;
    margin: 0;
    text-align: center;
    font-family: "Cinzel", serif;
    font-weight: 500;
    color: var(--title-blue);
    line-height: 1;
  }
  .title-line-one {
    display: block;
    font-size: 90px;
    letter-spacing: 0.22em;
    margin-right: -0.22em;
  }
  .title-line-two {
    display: block;
    margin-top: 46px;
    font-size: 118px;
    letter-spacing: 0.1em;
    margin-right: -0.1em;
  }
  .tagline {
    position: absolute;
    left: 0;
    right: 0;
    top: 372px;
    margin: 0;
    text-align: center;
    font-family: "Cinzel", serif;
    font-weight: 400;
    font-size: 34px;
    line-height: 36px;
    letter-spacing: 0.14em;
    color: var(--tag-mauve);
  }
  .boat-scene {
    position: absolute;
    left: 0;
    top: 500px;
    width: 800px;
    height: 600px;
    background:
      linear-gradient(to bottom, var(--paper) 0%, rgba(250,250,251,0) 22%, rgba(250,250,251,0) 78%, var(--paper) 100%),
      linear-gradient(170deg, var(--water-light) 0%, var(--hull-dark) 40%, var(--hull-dark) 55%, var(--water-mid) 72%, var(--water-light) 100%);
  }
  .author {
    position: absolute;
    left: 0;
    right: 0;
    top: 1136px;
    margin: 0;
    text-align: center;
    font-family: "Montserrat", sans-serif;
    font-weight: 600;
    font-size: 34px;
    letter-spacing: 0.42em;
    margin-right: -0.42em;
    color: var(--author-slate);
  }
</style>
</head>
<body>
  <main class="cover">
    <h1 class="title">
      <span class="title-line-one">QUIET</span>
      <span class="title-line-two">HARBORS</span>
    </h1>
    <p class="tagline">NOTES FROM A RESTLESS<br>PULPIT TODAY</p>
    <div class="boat-scene" role="img" aria-label="Dark rowing boat resting on calm pale water, tethered to a small float, with its reflection below"></div>
    <p class="author">AUTHOR NAME</p>
  </main>
</body>
</html>
```